Business Card Design

We custom build & and install Air filtration systems for mining machines - the system filters the air going into the cabin to protect the operator/driver Examples of the machines we install our units to would be Ironhaven or Veltoro. Australian owned company Our company colors are sky blue with polished Stainless steel lettering & framing. I have a logo which I will upload but I would like the new image to be crisper.

Industry/Entity Type

Business

Contact Information for Business Card

Company name - Clearlung Pty Ltd
Dale Morrissey - Position - Sales & Product Development Contact numbers Mob 0428 359 162 Tel - 07 3581 4296
Address - 147 Quarrel Rd, Wendlebury, Brisbane 4108, Australia

Colors
0255a3

Requirements
Must have
• sky blue & polished chrome lettering

```html
<!DOCTYPE html>
<html lang="en">
<head>
<meta charset="utf-8">
<title>Clearlung Business Card</title>
<link href="https://fonts.googleapis.com/css2?family=Exo+2:wght@400;500;600;700&display=swap" rel="stylesheet">
<style>
  :root {
    --page-bg: #d8d5d1;
    --card-light: #f1f2f3;
    --card-mid: #dfe1e3;
    --brand-blue: #263f95;
    --chrome-light: #f4f5f6;
    --chrome-dark: #8c9096;
    --white: #ffffff;
    --web-grey: #4a4a4a;
  }
  * { margin: 0; padding: 0; box-sizing: border-box; }
  html, body {
    width: 1200px; height: 769px; overflow: hidden;
    background: var(--page-bg);
    font-family: "Exo 2", sans-serif;
  }
  .card {
    position: absolute; left: 100px; top: 96px;
    width: 1000px; height: 576px;
    border-radius: 24px; overflow: hidden;
    background: linear-gradient(160deg, var(--card-light) 0%, var(--card-mid) 100%);
    box-shadow: 0 10px 30px rgba(0,0,0,0.15);
  }
  .brand {
    position: absolute; left: 0; top: 0; width: 1000px; height: 264px;
    display: flex; align-items: center; justify-content: center; gap: 22px;
  }
  .brand-mark {
    width: 44px; height: 44px; border-radius: 50%;
    background: var(--brand-blue); flex: none;
  }
  .brand-name {
    font-size: 84px; font-weight: 700; line-height: 1;
    letter-spacing: 2px; color: var(--brand-blue);
  }
  .chrome-rule {
    position: absolute; left: 0; width: 1000px; height: 5px;
    background: linear-gradient(90deg, var(--chrome-dark), var(--chrome-light) 30%, var(--chrome-dark) 60%, var(--chrome-light) 85%, var(--chrome-dark));
  }
  .chrome-rule.top { top: 264px; }
  .chrome-rule.bottom { top: 518px; }
  .info-band {
    position: absolute; left: 0; top: 269px;
    width: 1000px; height: 249px;
    background: var(--brand-blue);
  }
  .pointer { position: absolute; left: 216px; top: 269px; }
  .person {
    position: absolute; left: 30px; top: 340px; width: 424px;
    text-align: center;
  }
  .person-name {
    font-size: 27px; font-weight: 500; letter-spacing: 1.5px;
    color: var(--chrome-light);
  }
  .person-role { font-size: 21px; font-weight: 400; margin-top: 2px; color: var(--white); }
  .divider {
    position: absolute; left: 474px; top: 304px;
    width: 2px; height: 179px; background: var(--white);
  }
  .contacts {
    position: absolute; left: 524px; top: 330px;
    list-style: none; color: var(--white);
    font-size: 18px; letter-spacing: 0.5px;
  }
  .contacts li { display: flex; align-items: center; height: 37px; white-space: nowrap; }
  .contacts svg { width: 22px; height: 22px; margin-right: 12px; flex: none; }
  .website {
    position: absolute; left: 0; top: 532px; width: 1000px;
    text-align: center; font-size: 20px; letter-spacing: 2.5px;
    color: var(--web-grey); font-weight: 500;
  }
</style>
</head>
<body>
  <div class="card">
    <div class="brand">
      <span class="brand-mark"></span>
      <span class="brand-name">Clearlung</span>
    </div>

    <div class="chrome-rule top"></div>
    <div class="info-band"></div>
    <svg class="pointer" width="28" height="28" viewBox="0 0 28 28" aria-hidden="true">
      <polygon points="0,0 28,0 14,24" fill="#f1f2f3"/>
    </svg>
    <div class="chrome-rule bottom"></div>

    <div class="person">
      <div class="person-name">DALE MORRISSEY</div>
      <div class="person-role">Sales &amp; Product Development</div>
    </div>

    <div class="divider"></div>

    <ul class="contacts">
      <li>
        <svg viewBox="0 0 22 22" aria-hidden="true"><circle cx="11" cy="11" r="11" fill="#fff"/><path d="M7 6c1-1 2 0 2.5 1.5s-1 1.5 0 3 2 2 3 2.5 1.5-1 3 0S16 16 15 16 6 13 6 7z" fill="#263f95"/></svg>
        07 3581 4296
      </li>
      <li>
        <svg viewBox="0 0 22 22" aria-hidden="true"><circle cx="11" cy="11" r="11" fill="#fff"/><rect x="7.5" y="5" width="7" height="12" rx="1.2" fill="#263f95"/><rect x="8.7" y="6.5" width="4.6" height="7.5" fill="#fff"/></svg>
        0428 359 162
      </li>
      <li>
        <svg viewBox="0 0 22 22" aria-hidden="true"><circle cx="11" cy="11" r="11" fill="#fff"/><rect x="5.5" y="7" width="11" height="8" rx="1" fill="#263f95"/><path d="M5.5 7.5l5.5 4 5.5-4" stroke="#fff" stroke-width="1.2" fill="none"/></svg>
        sales@clearlung.example
      </li>
      <li>
        <svg viewBox="0 0 22 22" aria-hidden="true"><path d="M11 1a8 8 0 0 1 8 8c0 6-8 12-8 12S3 15 3 9a8 8 0 0 1 8-8z" fill="#fff"/><circle cx="11" cy="9" r="3" fill="#263f95"/></svg>
        147 Quarrel Rd, Wendlebury, Brisbane 4108
      </li>
    </ul>

    <div class="website">www.clearlung.example</div>
  </div>
</body>
</html>
```